New Book Cover Design Project for book about Trade Blend

DetWe need a book cover (front, back, spine) for a new book entitled ‘Trade Blend’’ and subtitled “beyond old rules toward real buyer wishes” (inverted commas not to be part of the title and subtitle). The author is Malcolm Ferrisby. The publisher is Tessellane Insights. The finished size of the paperback version will be 5" x 8" (127 x 203.2 mm). There will be paperback, hardback, and e-book versions. The final number of pages is expected to be in the region of 80 pages. Text for the back cover is in an attached document. At the bottom of the back cover should be publisher logo (rectangular) on the left and space for the ISBN bar code on the right. The design should be original and not include any stock images that have been created by someone else or may require obtaining a copyright licence to use. Symbols in common use and not copyrighted are probably ok. There are no required images, photographs or symbols except the publisher logo at the left bottom of the back cover. Spine lettering should be UK/US style with the top of the writing nearest the front cover. The designer is free to be creative using appropriate diagrams, symbols or abstract designs. A copy of the publisher logo is attached. Designers are assured that when evaluating designs absolutely no notice whatsoever is taken of a designer's Pixel Forum ranking or status; We are completely output driven, so what matters is the design, not the ranking or status of the designer. In a similar way, designs are not evaluated as 'good' or 'bad' - the winning design will be chosen after review by a design review panel and is not decided arbitrarily by a single person. All submitted designs should be capable of effective copyright assignment. Designs submitted for consideration should include front cover, spine, and back cover.
Candidate Trade Blend words that can be included in designs, if the designer wishes, include: product, place, promotion, price, consumer, company objectives, participants, physical evidence, process of service assembly, battery life, usability, security, fashion, design, brand, appearance, health, obedience, sustainability, accessibility, value, idea, information operation, beliefs, vectors.

Target Market(s)

Academics, teachers, text book writers, and students concerned with marketing.

Industry/Entity Type

Education

Font styles to use
Serif

Requirements
Must have
• • Author on the front cover and the spine. Templates have been added to the brief for the cover with spine for a 80 page book. There are .indd and .pdf templates that can be used. the .indd and .pdf templates show where the ISBN blocks should go. The other .PDF templates have the ISBN in the wrong place (middle of the lower back cover) but have more information about the meanings of template markings. Bleeds - PLEASE NOTE - the cover printing is not exact - there is minor variation when the printers print the covers. Therefore do not have solid blocks of colour that go to the edges of the spine or spine and cover pages with different blocks of colour - solid blocks of colour may go round the spine folds a little bit! See the templates - they indicate the areas for possible printing imprecision. The ISBN numbers in the template file names are what will be used - perfect is for the paperback and case is for the hardback.
Nice to have
• • It is not necessary to have the subtitle on the spine. The final book size may not be 80 pages, therefore the spine width may change, but not by much. • Use only standard fonts.
Should not have
• • Ideally, stock images should not be used as we cannot control other uses of images created by other sources, thus potentially damaging the book branding. I don't like solid black cover or spine backgrounds.

```html
<!DOCTYPE html>
<html lang="en">
<head>
<meta charset="utf-8">
<title>Trade Blend – Book Cover</title>
<link rel="stylesheet" href="https://fonts.googleapis.com/css2?family=EB+Garamond:wght@400;500;600;700&display=swap">
<style>
  :root {
    --paper: #ffffff;
    --ink: #1a1a1a;
    --author-panel: #bde3f6;
    --publisher-blue: #1b6db5;
    --frame: #222222;
    --tone-green: rgba(156, 193, 60, 0.45);
    --tone-orange: rgba(242, 154, 58, 0.45);
    --tone-yellow: rgba(245, 224, 74, 0.45);
    --tone-teal: rgba(20, 163, 160, 0.40);
    --tone-blue: rgba(28, 143, 208, 0.40);
    --tone-red: rgba(232, 80, 43, 0.35);
  }
  * { margin: 0; padding: 0; box-sizing: border-box; }
  html, body { width: 1200px; height: 958px; overflow: hidden; background: var(--paper); }
  .cover {
    position: relative;
    width: 1200px;
    height: 958px;
    background: var(--paper);
    color: var(--ink);
    font-family: "EB Garamond", Garamond, serif;
    overflow: hidden;
  }

  /* Artwork areas */
  .art-top {
    position: absolute; left: 0; top: 0; width: 1200px; height: 112px;
    background:
      linear-gradient(180deg, rgba(255,255,255,0) 0%, rgba(255,255,255,0) 35%, var(--paper) 100%),
      linear-gradient(90deg, var(--tone-green) 0%, var(--tone-orange) 30%, var(--tone-yellow) 50%, var(--tone-teal) 75%, var(--tone-blue) 100%);
  }
  .art-front {
    position: absolute; left: 612px; top: 334px; width: 588px; height: 496px;
    background:
      radial-gradient(ellipse at 50% 25%, rgba(255,255,255,0) 0%, rgba(255,255,255,0) 40%, var(--paper) 75%),
      linear-gradient(135deg, var(--tone-teal) 0%, var(--tone-yellow) 40%, var(--tone-red) 65%, var(--tone-orange) 85%, var(--tone-green) 100%);
  }

  /* Back cover */
  .back-blurb { position: absolute; left: 62px; top: 132px; width: 482px; }
  .back-blurb h2 {
    font-weight: 600; font-size: 22px; letter-spacing: 0.5px;
    text-align: center; line-height: 1; margin-bottom: 10px;
  }
  .back-blurb p {
    font-size: 18.6px; line-height: 21px; text-align: justify;
  }
  .author-panel {
    position: absolute; left: 62px; top: 572px; width: 488px; height: 169px;
    background: var(--author-panel);
  }
  .author-photo {
    position: absolute; left: 4px; top: 5px; width: 115px; height: 159px;
    background: linear-gradient(160deg, #9fb7c9 0%, #8a8d8f 45%, #4c5562 100%);
  }
  .author-bio { position: absolute; left: 131px; top: 4px; width: 351px; }
  .author-bio h2 { font-weight: 600; font-size: 22px; letter-spacing: 0.4px; line-height: 1.15; margin-bottom: 3px; }
  .author-bio p { font-size: 17.6px; line-height: 21px; text-align: justify; }

  .publisher {
    position: absolute; left: 66px; top: 832px; height: 40px;
    display: flex; align-items: center; gap: 10px;
    font-weight: 500; font-size: 26px; color: var(--publisher-blue);
  }
  .publisher-square { width: 18px; height: 18px; background: var(--publisher-blue); }
  .isbn-space {
    position: absolute; left: 320px; top: 768px; width: 230px; height: 138px;
    border: 1px solid var(--frame); background: var(--paper);
  }

  /* Spine */
  .spine {
    position: absolute; left: 589px; top: 322px; width: 22px; height: 320px;
    writing-mode: vertical-rl;
    display: flex; align-items: center; gap: 10px;
  }
  .spine-title { font-weight: 600; font-size: 19px; letter-spacing: 3px; }
  .spine-dot {
    width: 13px; height: 13px; border-radius: 50%;
    background: radial-gradient(circle at 40% 40%, #e6f3ff, #7fb4ea);
    border: 1px solid #6a9fd6;
  }
  .spine-author { font-weight: 500; font-size: 14px; letter-spacing: 2px; }

  /* Front cover */
  .front-title {
    position: absolute; left: 660px; top: 130px; width: 476px;
    font-weight: 600; font-size: 86px; line-height: 1; letter-spacing: -0.5px;
    white-space: nowrap;
  }
  .front-subtitle {
    position: absolute; left: 662px; top: 242px; width: 476px;
    font-size: 26px; line-height: 1.1; white-space: nowrap;
  }
  .front-author {
    position: absolute; left: 660px; top: 838px; width: 476px;
    text-align: center; font-weight: 600; font-size: 38px; line-height: 1;
  }
</style>
</head>
<body>
<main class="cover">
  <div class="art-top" role="img" aria-label="Abstract artwork band of flowing colour lines along the top edge"></div>
  <div class="art-front" role="img" aria-label="Abstract artwork of a colourful orb resting on flowing colour ribbons"></div>

  <section class="back-blurb">
    <h2>About the Book</h2>
    <p>This book has been inspired by the many textbooks, classes and student work about trade blend, which simply present or teach trade blend as 4Ps - very often not even acknowledging where those 4Ps came from. This approach is simply unacceptable academic work - no discussion of the extensive research from the 1920s onwards, about what is needed for effective marketing and trade blend. In several ways, this is a thoroughly radical book pushing against the common approach of simply teaching about simplistic 4Ps. Many students produce a trade blend for a company; they shouldn't. The book provides a solid example of what academics often call 'critical thinking'. Other ways in which the book is radical, is that it shows that trade blend is not only for products and services; it is also for ideas. The book discusses the idea that marketing can be seen as a branch of information warfare. Positioning should be included in trade blend considerations. Trade blend should not only be considered for legitimate products, services, and ideas; it is relevant also for those who trade in legal or mixed legal and illegal products and services. Examples are explored in the book.</p>
  </section>

  <section class="author-panel">
    <div class="author-photo" role="img" aria-label="Portrait photograph of the author"></div>
    <div class="author-bio">
      <h2>About the Author</h2>
      <p>Malcolm Ferrisby has extensive experience in industry, academia, and a variety of NGOs working in human and civil rights. Within those contexts, he has a lot of marketing experience as practitioner, academic, and external examiner – contributing to the radical nature of this book.</p>
    </div>
  </section>

  <div class="publisher">
    <span>Tessellane Insights</span>
    <span class="publisher-square"></span>
  </div>
  <div class="isbn-space"></div>

  <div class="spine">
    <span class="spine-title">Trade Blend</span>
    <span class="spine-dot"></span>
    <span class="spine-author">Malcolm Ferrisby</span>
  </div>

  <h1 class="front-title">Trade Blend</h1>
  <p class="front-subtitle">beyond old rules toward real buyer wishes</p>
  <p class="front-author">Malcolm Ferrisby</p>
</main>
</body>
</html>
```